Luxury Candle Startup Needs Modern Packaging Box & Matching Label Design

We are Lumavale, a luxury candle company about to launch in Australia and we need a box packaging design that is modern, minimalist, and feminine. Our target audience are females, mostly mothers, within the age range of 25-45 who are looking for high quality, handmade luxurious products. Our company is going to have a large social media presence with new mothers as we are going to show our journey with starting a business whilst on maternity leave. We would like the arch shape incorporated into the box packaging as it is beautiful and symbolises moving into a new phase in life which really represents the brand. We would like for the packaging box to be a simple white box with a sleeve insert over the box with the design to make printing easier. Our colour inspiration are very earthy colours and would like the sleeve colour to be easily changed according to the scent. For example dusky rose coloured sleeve for rose patchouli and amber scent, light coffee coloured sleeve for coffee bean cacao scent etc. Please see uploaded files for inspiration, our logo, and the type of candle jars used.
The box dimensions are:
External Dimension: 95mmW x 95mmL x 116mmH
We look forward to seeing your amazing designs!

```html
<!DOCTYPE html>
<html lang="en">
<head>
<meta charset="utf-8">
<title>Lumavale – Candle Box Dieline</title>
<link rel="stylesheet" href="https://fonts.googleapis.com/css2?family=Cormorant+Garamond:wght@400&family=Jost:wght@400;500&family=Allura&display=swap">
<style>
  :root {
    --backdrop: #8f8f88;
    --board: #ffffff;
    --pattern: #efefef;
    --sleeve-tail: #e6e6e6;
    --rose: #dcc0b8;
    --gold: #d9b66a;
    --ink-soft: #b4b4b4;
    --ink-mid: #9a9a9a;
  }
  html, body {
    margin: 0;
    padding: 0;
    width: 1200px;
    height: 2283px;
    overflow: hidden;
    background: var(--backdrop);
  }
  .dieline {
    display: block;
    width: 1200px;
    height: 2283px;
  }
  .board { fill: var(--board); }
  .pattern-field { fill: var(--pattern); }
  .sleeve-tail { fill: var(--sleeve-tail); }
  .sleeve-label { fill: var(--rose); }
  .label-frame { fill: none; stroke: var(--gold); stroke-width: 1.4; }
  .label-rule { stroke: var(--gold); stroke-width: 1.2; }
  .brand-name {
    font-family: "Cormorant Garamond", serif;
    font-weight: 400;
    letter-spacing: 1px;
    text-anchor: middle;
  }
  .brand-name--grey { fill: var(--ink-soft); font-size: 27px; }
  .brand-name--gold { fill: var(--gold); font-size: 22px; }
  .tagline {
    font-family: "Jost", sans-serif;
    font-weight: 500;
    text-anchor: middle;
  }
  .tagline--grey { fill: var(--ink-soft); font-size: 8.5px; letter-spacing: 2px; }
  .tagline--gold { fill: var(--gold); font-size: 5.5px; letter-spacing: 1.2px; }
  .scent-name {
    font-family: "Jost", sans-serif;
    font-weight: 500;
    font-size: 7px;
    letter-spacing: 1.5px;
    fill: var(--gold);
    text-anchor: middle;
  }
  .side-copy {
    font-family: "Jost", sans-serif;
    font-weight: 500;
    fill: var(--ink-mid);
    text-anchor: middle;
  }
  .side-copy--large { font-size: 13px; letter-spacing: 4px; }
  .side-copy--small { font-size: 6.5px; letter-spacing: 1.5px; }
  .script-note {
    font-family: "Allura", cursive;
    font-size: 15px;
    fill: var(--ink-mid);
    text-anchor: middle;
  }
</style>
</head>
<body>
<svg class="dieline" viewBox="60 670 1200 2283" xmlns="http://www.w3.org/2000/svg">

  <!-- Front panel with glue flap and tuck flap -->
  <g class="panel panel--front">
    <path class="board" d="M174 1468 L112 1488 Q107 1490 107 1500 L107 1763 L174 1785 Z"/>
    <path class="board" d="M174 1785 L174 1178 Q174 1153 199 1153 L408 1153 Q433 1153 433 1178 L433 1785 Z"/>
    <g role="img" aria-label="Fine white-on-grey mandala line pattern">
      <rect class="pattern-field" x="174" y="1208" width="259" height="577"/>
    </g>
    <path class="board" d="M245 1785 L245 1543 A60 60 0 0 1 365 1543 L365 1785 Z"/>
    <rect class="board" x="174" y="1615" width="259" height="82"/>
    <text class="brand-name brand-name--grey" x="303" y="1652">LUMAVALE</text>
    <text class="tagline tagline--grey" x="303" y="1670">LUXURY FRAGRANCE</text>
    <text class="tagline tagline--grey" x="303" y="1684" style="font-size:7px">AUSTRALIA</text>
  </g>

  <!-- Side panel with dust flaps -->
  <g class="panel panel--side-left">
    <path class="board" d="M433 1283 L622 1283 Q632 1283 636 1295 L663 1390 L693 1422 L693 1970 L500 1970 Q492 1970 490 1960 L465 1866 L433 1840 Z"/>
    <text class="side-copy side-copy--large" x="565" y="1658">SOY CANDLE</text>
    <text class="script-note" x="565" y="1674">Hand Poured</text>
  </g>

  <!-- Back panel carrying the scent sleeve -->
  <g class="panel panel--back">
    <path class="board" d="M693 1468 L953 1468 L953 2070 Q953 2095 928 2095 L718 2095 Q693 2095 693 2070 Z"/>
    <g role="img" aria-label="Fine white-on-grey mandala line pattern">
      <rect class="pattern-field" x="693" y="1468" width="260" height="317"/>
    </g>
    <rect class="board" x="693" y="1615" width="260" height="82"/>
    <rect class="sleeve-tail" x="733" y="1785" width="179" height="685"/>
    <path class="sleeve-label" d="M733 1785 L733 1569 A89.5 89.5 0 0 1 912 1569 L912 1785 Z"/>
    <path class="label-frame" d="M744 1772 L744 1572 A78.5 78.5 0 0 1 901 1572 L901 1772 Z"/>
    <text class="brand-name brand-name--gold" x="823" y="1659">LUMAVALE</text>
    <text class="tagline tagline--gold" x="823" y="1670">LUXURY FRAGRANCE</text>
    <text class="tagline tagline--gold" x="823" y="1679" style="font-size:4.5px">AUSTRALIA</text>
    <line class="label-rule" x1="813" y1="1704" x2="833" y2="1704"/>
    <text class="scent-name" x="823" y="1724">ROSE PATCHOULI</text>
  </g>

  <!-- Side panel with dust flaps -->
  <g class="panel panel--side-right">
    <path class="board" d="M953 1422 L983 1390 L1010 1295 Q1014 1283 1024 1283 L1214 1283 L1214 1820 L1186 1862 L1160 1960 Q1157 1970 1148 1970 L953 1970 Z"/>
    <text class="side-copy side-copy--small" x="1088" y="1655">300GRAMS</text>
    <text class="side-copy side-copy--small" x="1088" y="1667">50 HOUR BURN TIME</text>
  </g>

</svg>
</body>
</html>
```